Insurance Agency website design for Brellow Cover Insurance, LP

Build a website for Brellow Cover Insurance, LP which sells Homeowners, Auto, Renters, Condo, Flood, Disability, Life, Umbrella, and health insurance. We need the coolest insurance agency website out there to get quotes, contact us, or get additional information. Please list the following insurance companies we work with: Varnix, Ostle, Meridale Mutual, Quillor, Dunmarrow, KGZ, and Pellwick.

Make a design similar to https://www.fernagentry.com/

Selling personal insurance policies

```html
<!DOCTYPE html>
<html lang="en">
<head>
<meta charset="utf-8">
<title>Brellow Cover Insurance, LP</title>
<link href="https://fonts.googleapis.com/css2?family=Poppins:wght@400;500;600;700&family=Roboto:wght@400;500;700&display=swap" rel="stylesheet">
<style>
:root{
  --green:#8cc11f;
  --blue:#1a6fc4;
  --ink:#111418;
  --text:#555b63;
  --light:#f2f2f2;
  --footer:#0b1522;
  --line:#e3e6ea;
  --white:#fff;
}
*{box-sizing:border-box;margin:0;padding:0}
html,body{width:1200px;height:3885px;overflow:hidden}
body{font-family:"Roboto",sans-serif;color:var(--ink);background:var(--white);position:relative}
.abs{position:absolute}

/* header */
.topbar{left:671px;top:0;width:529px;height:27px;background:var(--blue);color:#fff;font-size:13px;font-weight:500;display:flex;align-items:center}
.topbar span{display:flex;align-items:center;gap:7px;height:100%}
.topbar .mail{padding-left:36px;width:278px;border-right:1px solid rgba(255,255,255,.35)}
.topbar .tel{padding-left:22px}
.brand{display:flex;align-items:center;gap:12px}
.brand-mark{width:44px;height:44px;background:var(--green);border-radius:6px}
.brand-name{font-family:"Poppins",sans-serif;font-weight:600;color:var(--ink);line-height:1.2}
.site-header .brand{left:112px;top:20px}
.site-header .brand-name{font-size:17px}
.nav{left:583px;top:58px;display:flex;gap:31px;font-size:13px;font-weight:500;text-transform:uppercase}
.nav a{color:var(--ink);text-decoration:none}
.nav a.active{color:var(--green)}
.btn{display:inline-flex;align-items:center;justify-content:center;background:var(--green);color:#fff;font-family:"Roboto",sans-serif;font-weight:700;text-transform:uppercase;letter-spacing:.4px;border-radius:3px;text-decoration:none}
.header-cta{left:947px;top:46px;width:141px;height:38px;font-size:13px}

/* hero */
.hero{left:0;top:100px;width:1200px;height:584px;background:linear-gradient(100deg,#2e3a2a 0%,#4e5a44 35%,#6d7560 55%,#4a5e35 80%,#2f4a20 100%)}
.hero-title{left:110px;top:266px;color:#fff;font-family:"Poppins",sans-serif;font-size:44px;line-height:51px;font-weight:600}
.hero-title .light{font-weight:400;display:block}
.hero-cta{left:110px;top:455px;width:170px;height:53px;font-size:16px}

/* partners */
.partners{left:0;top:684px;width:1200px;height:303px;background:var(--light)}
.eyebrow{font-size:16px;font-weight:700;color:var(--blue);text-transform:uppercase;display:flex;align-items:center;gap:12px}
.eyebrow::before,.eyebrow::after{content:"";width:46px;height:3px;background:var(--blue)}
.eyebrow.left::before{display:none}
.eyebrow.left::after{width:74px}
.section-title{font-family:"Roboto",sans-serif;font-size:35px;font-weight:400;text-transform:uppercase;color:var(--ink)}
.section-title b{font-weight:700}
.center{left:0;width:1200px;display:flex;justify-content:center}
.partner-row{left:119px;top:154px;display:flex;gap:33px}
.partner{width:166px;height:86px;background:#fff;border-radius:8px;box-shadow:0 2px 8px rgba(0,0,0,.08);display:flex;align-items:center;justify-content:center;font-family:"Poppins",sans-serif;font-weight:600;font-size:16px;color:#2a3440}
.arrow{top:176px}

/* about */
.about-photo-main{left:112px;top:1081px;width:423px;height:606px;background:linear-gradient(150deg,#cfd4d2,#8f9892 50%,#5c6260)}
.about-photo-small{left:437px;top:1523px;width:347px;height:271px;background:linear-gradient(135deg,#b9b4ab,#8d8578 55%,#6a655d);border:4px solid #fff}
.about-text{left:600px;top:1105px;width:489px}
.about-text h2{font-size:30px;font-weight:400;text-transform:uppercase;margin:18px 0 27px;white-space:nowrap}
.about-text h2 b{font-weight:700}
.about-text p{font-size:13.5px;line-height:24px;color:var(--text);text-align:justify;margin-bottom:12px}
.about-text p b{color:var(--ink);font-weight:500}
.about-cta{left:600px;top:1420px;width:152px;height:44px;font-size:14px}

/* lines */
.promo{top:1931px;height:252px;width:593px;border-radius:14px}
.promo.business{left:0;background:var(--blue)}
.promo.personal{left:607px;background:var(--green)}
.promo-person{top:1862px;height:321px;width:220px}
.promo-person.biz{left:10px;background:linear-gradient(180deg,#d9c3ad 0%,#6f8f74 45%,#2a3038 100%);border-radius:110px 110px 0 14px}
.promo-person.pers{left:625px;background:linear-gradient(180deg,#5a3a2a 0%,#c59a7c 40%,#6b6f74 100%);border-radius:110px 110px 0 0}
.promo-copy{color:#fff}
.promo-copy h3{font-size:20px;font-weight:700;margin-bottom:18px}
.promo-copy p{font-size:13.5px;line-height:20px;width:300px;margin-bottom:20px}
.promo-copy .btn{height:43px;padding:0 19px;font-size:13.5px}

/* services */
.service-grid{left:118px;top:2392px;display:grid;grid-template-columns:repeat(4,212px);column-gap:38px;row-gap:39px}
.service{height:192px;background:#fff;border:1px solid var(--line);box-shadow:0 0 0 6px #f6f7f8;display:flex;flex-direction:column;align-items:center;justify-content:flex-end;padding-bottom:40px;gap:20px}
.service svg{width:70px;height:62px;stroke:var(--blue);fill:none;stroke-width:2.4;stroke-linecap:round;stroke-linejoin:round}
.service span{font-size:18px;font-weight:500}

/* contact */
.contact{left:0;top:2920px;width:1200px;height:522px;background:linear-gradient(100deg,#86bd24 0%,#5fa54a 45%,#2f80b8 75%,#1a6fc4 100%)}
.contact-copy{left:112px;top:3018px;width:395px;color:#fff}
.contact-copy .eyebrow{color:#fff}
.contact-copy .eyebrow::after{background:#fff}
.contact-copy h2{font-size:33px;font-weight:400;text-transform:uppercase;margin:6px 0 20px}
.contact-copy h2 b{font-weight:700}
.contact-copy p{font-size:13.5px;line-height:22px;margin-bottom:14px}
.quote-form{left:600px;top:2992px;width:488px;height:525px;background:#fff;padding:44px 25px 0;z-index:2}
.quote-form h3{font-size:18px;font-weight:500;text-align:center;line-height:27px;margin-bottom:40px}
.field{height:46px;border:1px solid #cfd3d8;background:#fafafa;border-radius:3px;font-size:12.5px;color:#8a9099;padding:15px;margin-bottom:19px}
.field-pair{display:flex;gap:14px}
.field-pair .field{flex:1}
.field.message{height:88px}
.submit{width:100%;height:48px;font-size:16px;text-transform:none;font-weight:500;margin-top:13px}

/* footer */
.site-footer{left:0;top:3442px;width:1200px;height:443px;background:var(--footer);color:#fff}
.site-footer .brand{left:112px;top:150px}
.site-footer .brand-mark{width:70px;height:70px}
.site-footer .brand-name{color:#fff;font-size:22px}
.socials{left:173px;top:250px;display:flex;gap:10px}
.socials i{width:30px;height:30px;border:1.5px solid #fff;border-radius:50%;display:block}
.socials i.on{background:var(--green);border-color:var(--green)}
.foot-col h4{font-size:16px;font-weight:500;margin-bottom:20px}
.foot-col a{display:block;color:#fff;text-decoration:none;font-size:13px;line-height:25.5px}
.contact-item{display:flex;gap:12px;margin-bottom:14px;font-size:13px;line-height:20px}
.contact-item b{display:block;font-weight:500}
.contact-item svg{width:12px;height:12px;margin-top:4px;flex:none;fill:var(--green)}
.to-top{left:1107px;top:3793px;width:34px;height:34px;border-radius:50%;background:var(--blue);display:flex;align-items:center;justify-content:center;z-index:2}
.copyright{left:0;top:3836px;width:1200px;text-align:center;font-size:14px;color:#fff;z-index:2}
</style>
</head>
<body>

<header class="site-header">
  <div class="abs topbar">
    <span class="mail"><svg width="13" height="13" viewBox="0 0 24 24" fill="none" stroke="#fff" stroke-width="2"><rect x="3" y="5" width="18" height="14" rx="2"/><path d="M3 7l9 6 9-6"/></svg>info@brellowcover.com</span>
    <span class="tel"><svg width="12" height="12" viewBox="0 0 24 24" fill="#fff"><path d="M6.6 10.8a15.1 15.1 0 006.6 6.6l2.2-2.2a1 1 0 011-.25 11.4 11.4 0 003.6.57 1 1 0 011 1V20a1 1 0 01-1 1A17 17 0 013 4a1 1 0 011-1h3.5a1 1 0 011 1c0 1.25.2 2.45.57 3.57a1 1 0 01-.25 1z"/></svg>(612) 555-0148</span>
  </div>
  <div class="abs brand">
    <div class="brand-mark"></div>
    <div class="brand-name">BRELLOW COVER<br>INSURANCE, LP</div>
  </div>
  <nav class="abs nav">
    <a class="active" href="#">Home</a><a href="#">About</a><a href="#">Insurance</a><a href="#">Contact</a>
  </nav>
  <a class="abs btn header-cta" href="#">Get a Quote</a>
</header>

<section>
  <div class="abs hero" role="img" aria-label="Smiling family of four standing on the lawn in front of their home"></div>
  <h1 class="abs hero-title">Protecting What<br>Matters Most –<span class="light">Get Covered Today!</span></h1>
  <a class="abs btn hero-cta" href="#">Get a Quote</a>
</section>

<section class="abs partners">
  <div class="abs center" style="top:49px"><div class="eyebrow">Our Partners</div></div>
  <div class="abs center" style="top:72px"><h2 class="section-title"><b>We Work</b> With</h2></div>
  <svg class="abs arrow" style="left:55px" width="22" height="40" viewBox="0 0 22 40"><path d="M19 3L3 20l16 17" stroke="#111" stroke-width="3" fill="none"/></svg>
  <div class="abs partner-row">
    <div class="partner">Varnix</div>
    <div class="partner">Meridale Mutual</div>
    <div class="partner">Quillor</div>
    <div class="partner">Dunmarrow</div>
    <div class="partner">KGZ</div>
  </div>
  <svg class="abs arrow" style="left:1123px" width="22" height="40" viewBox="0 0 22 40"><path d="M3 3l16 17L3 37" stroke="#111" stroke-width="3" fill="none"/></svg>
</section>

<section>
  <div class="abs about-photo-main" role="img" aria-label="Insurance agent with a tablet talking with two clients"></div>
  <div class="abs about-photo-small" role="img" aria-label="Three colleagues reviewing documents together at a table"></div>
  <div class="abs about-text">
    <div class="eyebrow left">About Us</div>
    <h2><b>Brellow Cover</b> Insurance, LP</h2>
    <p><b>Brellow Cover Insurance</b> is a full-service, independent insurance agency with over three decades of experience in delivering comprehensive insurance solutions to individuals.</p>
    <p>We proudly offer a diverse portfolio of products from more than 20 of the most reputable and financially secure companies in the industry. Our dedicated team of over 50 skilled professionals is committed to customizing these products and services to meet the unique needs of each client.</p>
  </div>
  <a class="abs btn about-cta" href="#">Learn More</a>
</section>

<section>
  <div class="abs promo business"></div>
  <div class="abs promo-person biz" role="img" aria-label="Smiling businesswoman holding a clipboard"></div>
  <div class="abs promo-copy" style="left:253px;top:1982px">
    <h3>Business Insurance</h3>
    <p>General Liability , Commercial Auto, Property, Workers' Comp and much more</p>
    <span class="btn" style="background:var(--green)">Find Business Insurance</span>
  </div>
  <div class="abs promo personal"></div>
  <div class="abs promo-person pers" role="img" aria-label="Smiling young woman looking at her phone"></div>
  <div class="abs promo-copy" style="left:871px;top:1982px">
    <h3>Personal Insurance</h3>
    <p>Auto Home Landlord Renters RV Watercrafts Umbrella and much more</p>
    <span class="btn" style="background:var(--blue)">Find Personal Insurance</span>
  </div>
</section>

<section>
  <div class="abs center" style="top:2275px"><div class="eyebrow">Our Services</div></div>
  <div class="abs center" style="top:2298px"><h2 class="section-title"><b>Type Of</b> Insurance</h2></div>
  <div class="abs service-grid">
    <div class="service"><svg viewBox="0 0 70 62"><path d="M8 38l6-16c1-3 3-4 6-4h30c3 0 5 1 6 4l6 16"/><rect x="4" y="36" width="62" height="14" rx="4"/><path d="M10 50v6h8v-6M52 50v6h8v-6M14 43h6M50 43h6M26 43h18"/></svg><span>Auto</span></div>
    <div class="service"><svg viewBox="0 0 70 62"><path d="M6 30L35 6l29 24"/><path d="M12 26v32h46V26"/><path d="M46 12V6h6v11"/><rect x="20" y="36" width="14" height="12"/><path d="M27 36v12M20 42h14M40 58V38h10v20"/></svg><span>Homeowners</span></div>
    <div class="service"><svg viewBox="0 0 70 62"><circle cx="44" cy="18" r="10"/><path d="M28 58c0-12 7-20 16-20s16 8 16 20"/><circle cx="16" cy="22" r="7"/><path d="M16 29v26M16 40h7M16 48h6"/></svg><span>Renters</span></div>
    <div class="service"><svg viewBox="0 0 70 62"><rect x="10" y="14" width="26" height="44"/><rect x="36" y="26" width="24" height="32"/><path d="M18 6v8M16 22h4M26 22h4M16 30h4M26 30h4M16 38h4M26 38h4M42 34h4M50 34h4M42 42h4M50 42h4M20 58v-8h6v8M4 58h62"/></svg><span>Condo</span></div>
    <div class="service"><svg viewBox="0 0 70 62"><path d="M14 28L35 10l21 18"/><path d="M19 24v16h32V24"/><path d="M31 40V31h8v9"/><path d="M4 48c5-4 9-4 14 0s9 4 14 0 9-4 14 0 9 4 14 0 6-3 6-3M4 57c5-4 9-4 14 0s9 4 14 0 9-4 14 0 9 4 14 0 6-3 6-3"/></svg><span>Flood</span></div>
    <div class="service"><svg viewBox="0 0 70 62"><circle cx="32" cy="8" r="5"/><path d="M32 14v18h16l6 16"/><path d="M32 22h12"/><path d="M26 26a16 16 0 1022 20"/></svg><span>Disability</span></div>
    <div class="service"><svg viewBox="0 0 70 62"><path d="M35 56S8 40 8 22a13 13 0 0127-6 13 13 0 0127 6c0 18-27 34-27 34z"/><path d="M16 30h10l4-8 6 16 4-8h12"/></svg><span>Life</span></div>
    <div class="service"><svg viewBox="0 0 70 62"><path d="M35 4l24 8v18c0 14-10 24-24 30C21 54 11 44 11 30V12z"/><path d="M35 20v20M25 30h20"/></svg><span>Health</span></div>
  </div>
</section>

<section>
  <div class="abs contact" role="img" aria-label="Soft green to blue band over a faint family photo"></div>
  <div class="abs contact-copy">
    <div class="eyebrow left">Contact Us</div>
    <h2><b>Get A</b> Quote</h2>
    <p>We believe that securing your home is one of the most important decisions you can make. Obtaining a comprehensive insurance quote is essential to understanding your coverage options and ensuring that your property is adequately protected against unforeseen events.</p>
    <p>Our team of experienced professionals is here to guide you through the process, helping you find the right policy that meets your specific needs and budget. Don't leave your home's safety to chance—get a quote today and take the first step towards peace of mind.</p>
  </div>
  <form class="abs quote-form">
    <h3>Fill In This Form Or Send Us An Email<br>With Your Inquiry</h3>
    <div class="field-pair"><div class="field">First Name</div><div class="field">First Name</div></div>
    <div class="field">Email Address</div>
    <div class="field">Phone Number</div>
    <div class="field message">Message</div>
    <div class="btn submit">Submit Now</div>
  </form>
</section>

<footer class="abs site-footer">
  <div class="abs brand">
    <div class="brand-mark"></div>
    <div class="brand-name">BRELLOW COVER<br>INSURANCE, LP</div>
  </div>
  <div class="abs socials" aria-label="Social links"><i></i><i class="on"></i><i></i><i></i></div>
  <div class="abs foot-col" style="left:460px;top:140px">
    <h4>Quick Links</h4><a href="#">Home</a><a href="#">About</a><a href="#">Insurance</a><a href="#">Contact</a>
  </div>
  <div class="abs foot-col" style="left:632px;top:140px">
    <h4>About Company</h4><a href="#">Support</a><a href="#">Privacy Policy</a><a href="#">Shipping Policy</a><a href="#">Terms &amp; Conditions</a><a href="#">Sitemap</a>
  </div>
  <div class="abs foot-col" style="left:841px;top:140px;width:250px">
    <h4>Contact Us</h4>
    <div class="contact-item"><svg viewBox="0 0 24 24"><path d="M6.6 10.8a15.1 15.1 0 006.6 6.6l2.2-2.2a1 1 0 011-.25 11.4 11.4 0 003.6.57 1 1 0 011 1V20a1 1 0 01-1 1A17 17 0 013 4a1 1 0 011-1h3.5a1 1 0 011 1c0 1.25.2 2.45.57 3.57a1 1 0 01-.25 1z"/></svg><div><b>Phone</b>(800) 555-0199</div></div>
    <div class="contact-item"><svg viewBox="0 0 24 24"><path d="M2 5h20v14H2zM2 6l10 7 10-7" stroke="#0b1522" stroke-width="1.5"/></svg><div><b>Email</b>info@brellowcover.com</div></div>
    <div class="contact-item"><svg viewBox="0 0 24 24"><path d="M12 2a7 7 0 00-7 7c0 5 7 13 7 13s7-8 7-13a7 7 0 00-7-7zm0 9.5A2.5 2.5 0 1112 6.5a2.5 2.5 0 010 5z"/></svg><div><b>Location</b>220 Harlow Ave, Suite 4, Fairview, NY 10090, USA</div></div>
  </div>
</footer>
<div class="abs to-top"><svg width="14" height="10" viewBox="0 0 14 10"><path d="M1 8l6-6 6 6" stroke="#fff" stroke-width="2" fill="none"/></svg></div>
<div class="abs copyright">2025 Copyright -  Brellow Cover Insurance | All Rights Reserved</div>

</body>
</html>
```